One of a kind service business!

We are the only ocean freight auditing company in the entire world that does what we do. We provide a innovative service in auditing our clients invoices for billing errors as it relates to the import and export of their products anywhere in the world. We'd like to retain the current logo - but we are open to any interesting concepts that can complete the card.

Target Market(s)

C-Level and Senior Financial executives

Industry/Entity Type

Auditing

Requirements
Must have

• ONE SIDED ONLY
Should not have
• no cartoonish images

```html
<!DOCTYPE html>
<html lang="en">
<head>
<meta charset="utf-8">
<title>Tidemark Review – Business Card Concepts</title>
<link href="https://fonts.googleapis.com/css2?family=Source+Sans+3:wght@400;600;700&display=swap" rel="stylesheet">
<style>
  :root {
    --stage: #eef1f4;
    --navy: #0c2a66;
    --ink: #13224a;
    --sea-light: #c9d9e6;
    --sea-mid: #8fb0c9;
    --sea-deep: #5f85a6;
    --blue-deep: #1d3d78;
    --blue-bright: #3f9fd6;
    --white: #ffffff;
    --accent: #1e9ad6;
  }
  * { margin: 0; padding: 0; box-sizing: border-box; }
  html, body { width: 1200px; height: 821px; overflow: hidden; }
  body {
    background: var(--stage);
    font-family: "Source Sans 3", "Myriad Pro", Arial, sans-serif;
    position: relative;
  }
  .card {
    position: absolute;
    width: 508px;
    height: 290px;
    border-radius: 18px;
    overflow: hidden;
    box-shadow: 0 2px 6px rgba(0,0,0,0.18);
  }
  .card--photo { left: 33px; top: 95px; }
  .card--blue {
    left: 643px; top: 90px;
    background: linear-gradient(160deg, var(--blue-deep) 0%, #2d64a3 50%, var(--blue-bright) 100%);
    color: var(--white);
  }
  .card--back { left: 409px; top: 462px; background: var(--white); }

  .photo-fill {
    position: absolute; inset: 0;
    background: linear-gradient(180deg, var(--sea-light) 0%, var(--sea-mid) 55%, var(--sea-deep) 100%);
  }
  .photo-veil {
    position: absolute; inset: 0;
    background: rgba(255,255,255,0.35);
  }

  .wordmark {
    position: absolute;
    left: 0; right: 0;
    display: flex; align-items: center; justify-content: center; gap: 12px;
    font-weight: 700;
    font-size: 50px;
    letter-spacing: 1px;
    line-height: 1;
  }
  .wordmark__square { width: 18px; height: 18px; background: currentColor; }
  .card--photo .wordmark { top: 42px; color: var(--navy); }
  .card--blue .wordmark { top: 50px; color: var(--white); }
  .card--back .wordmark { top: 120px; color: var(--navy); font-size: 54px; }

  .details {
    position: absolute;
    left: 0; right: 0; top: 134px;
    text-align: center;
    font-size: 15.5px;
    line-height: 23px;
  }
  .card--photo .details { color: var(--ink); }
  .card--blue .details { top: 142px; }
  .details__name { font-weight: 700; font-size: 15px; }
  .details__row { display: flex; justify-content: center; align-items: center; gap: 6px; }
  .details__row--gap { margin-top: 0; }
  .icon { width: 11px; height: 11px; fill: currentColor; flex: none; }
  .sep { margin: 0 4px; }
</style>
</head>
<body>

  <section class="card card--photo" aria-label="Business card, photo version">
    <div class="photo-fill" role="img" aria-label="Container ship sailing on open sea"></div>
    <div class="photo-veil"></div>
    <div class="wordmark"><span class="wordmark__square"></span>Tidemark Review</div>
    <div class="details">
      <p class="details__name">Daniel Moreau <span class="sep">|</span> CEO</p>
      <p>USA: +1 555 014 2290</p>
      <p class="details__row">
        <svg class="icon" viewBox="0 0 12 12"><path d="M2 1l2 0 1 3-1.3 1a6 6 0 0 0 3.3 3.3L8 7l3 1 0 2c0 .6-.5 1-1 1C5 11 1 7 1 2c0-.5.4-1 1-1z"/></svg>
        + 420 555 310 427
        <span class="sep"></span>
        <svg class="icon" viewBox="0 0 12 12"><rect x="3" y="0.5" width="6" height="11" rx="1"/><rect x="4" y="2" width="4" height="5" fill="#c9d9e6"/></svg>
        + 420 555 728 163
      </p>
      <p class="details__row">
        <svg class="icon" viewBox="0 0 12 12"><rect x="0.5" y="2" width="11" height="8"/><path d="M0.5 2l5.5 4 5.5-4" stroke="#c9d9e6" fill="none"/></svg>
        daniel@tidemarkreview.net
        <svg class="icon" viewBox="0 0 12 12"><circle cx="6" cy="6" r="5.5"/></svg>
        www.tidemarkreview.net
      </p>
      <p>Harbor Point Center - Quayside 18 - Portvale - Northland 240 17</p>
    </div>
  </section>

  <section class="card card--blue" aria-label="Business card, blue version">
    <div class="wordmark"><span class="wordmark__square"></span>Tidemark Review</div>
    <div class="details">
      <p class="details__name">Daniel Moreau <span class="sep">|</span> CEO</p>
      <p>USA: +1 555 014 2290</p>
      <p class="details__row">
        <svg class="icon" viewBox="0 0 12 12"><path d="M2 1l2 0 1 3-1.3 1a6 6 0 0 0 3.3 3.3L8 7l3 1 0 2c0 .6-.5 1-1 1C5 11 1 7 1 2c0-.5.4-1 1-1z"/></svg>
        + 420 555 310 427
        <span class="sep"></span>
        <svg class="icon" viewBox="0 0 12 12"><rect x="3" y="0.5" width="6" height="11" rx="1"/><rect x="4" y="2" width="4" height="5" fill="#2d64a3"/></svg>
        + 420 555 728 163
      </p>
      <p class="details__row">
        <svg class="icon" viewBox="0 0 12 12"><rect x="0.5" y="2" width="11" height="8"/><path d="M0.5 2l5.5 4 5.5-4" stroke="#2d64a3" fill="none"/></svg>
        daniel@tidemarkreview.net
        <svg class="icon" viewBox="0 0 12 12"><circle cx="6" cy="6" r="5.5"/></svg>
        www.tidemarkreview.net
      </p>
      <p>Harbor Point Center - Quayside 18 - Portvale - Northland 240 17</p>
    </div>
  </section>

  <section class="card card--back" aria-label="Business card, back side">
    <div class="wordmark"><span class="wordmark__square"></span>Tidemark Review</div>
  </section>

</body>
</html>
```